Professional Photography Business cards

I need business cards that include my logo which I have uploaded. I run a photography business. I am open to ideas but I would like one side to have my logo and the other side to have my contact info. I don't have a website made but I do own a website domain. I have uploaded 2 different logo color schemes. My business colors are Blue, black , and white.

Business Name
Business Phone Number
Business Email
Business Website address
Instagram

Industry/Entity Type

Professional Photography

Contact Information for Business Card

Phone Number: 916-384-7702 email: info@tlane-studio.example Instagram: @t.lanestudio website doman- www.tlane-studio.example

Requirements
Must have
• I like the idea of a business card with a full black background front and back of card. My colors must include royal blue, black, and white

```html
<!DOCTYPE html>
<html lang="en">
<head>
<meta charset="utf-8">
<title>T. Lane Studio — Business Cards</title>
<link rel="stylesheet" href="https://fonts.googleapis.com/css2?family=Montserrat:wght@400;500;600&display=swap">
<style>
  :root {
    --royal-blue: #0610a6;
    --ink: #0a0a0a;
    --paper: #ffffff;
    --backdrop: #e9e9ec;
  }
  * { box-sizing: border-box; margin: 0; padding: 0; }
  html, body {
    width: 1200px; height: 900px; overflow: hidden;
    background: var(--backdrop);
    font-family: "Montserrat", Arial, sans-serif;
  }
  .sheet {
    width: 1200px; height: 900px;
    display: flex; flex-direction: column; align-items: center; justify-content: center;
    gap: 40px;
  }
  .card {
    position: relative;
    width: 700px; height: 400px;
    overflow: hidden;
    box-shadow: 0 6px 18px rgba(0,0,0,.18);
  }
  .card--front { background: var(--royal-blue); }
  .card--back { background: var(--paper); }

  .brand {
    display: flex; align-items: center; gap: 16px;
    font-weight: 500; letter-spacing: .02em; white-space: nowrap;
  }
  .brand__dot { border-radius: 50%; flex: none; }

  .card--front .brand {
    position: absolute; left: 50%; top: 50%; transform: translate(-50%, -50%);
    color: var(--paper); font-size: 52px;
  }
  .card--front .brand__dot { width: 62px; height: 62px; border: 6px solid var(--paper); }

  .card--back .brand {
    position: absolute; right: 48px; top: 52px;
    color: var(--royal-blue); font-size: 34px;
  }
  .card--back .brand__dot { width: 42px; height: 42px; border: 4px solid var(--ink); }

  .wave { position: absolute; inset: 0; width: 100%; height: 100%; }

  .contact-list {
    position: absolute; left: 52px; top: 148px;
    list-style: none; display: flex; flex-direction: column; gap: 12px;
    z-index: 1;
  }
  .contact-list__item {
    display: flex; align-items: center; gap: 12px;
    font-size: 19px; line-height: 24px; color: var(--ink); white-space: nowrap;
  }
  .contact-list__icon {
    width: 26px; height: 26px; border-radius: 50%;
    background: var(--royal-blue);
    display: flex; align-items: center; justify-content: center; flex: none;
  }
  .contact-list__icon svg { width: 15px; height: 15px; }

  .social-handle {
    position: absolute; right: 40px; bottom: 70px;
    display: flex; align-items: center; gap: 10px;
    color: var(--paper); font-size: 19px; z-index: 1;
  }
  .social-handle__dot {
    width: 22px; height: 22px; border-radius: 50%; background: var(--paper);
  }
</style>
</head>
<body>
<main class="sheet">

  <section class="card card--front" aria-label="Card front">
    <div class="brand">
      <span class="brand__name">T. Lane Studio</span>
      <span class="brand__dot" aria-hidden="true"></span>
    </div>
  </section>

  <section class="card card--back" aria-label="Card back">
    <svg class="wave" viewBox="0 0 700 400" preserveAspectRatio="none" aria-hidden="true">
      <path d="M0 305 C200 305 370 275 505 222 C350 295 190 326 0 332 Z" fill="#0a0a0a"/>
      <path d="M0 340 C260 335 460 250 700 125 L700 400 L0 400 Z" fill="#0610a6"/>
    </svg>

    <div class="brand">
      <span class="brand__name">T. Lane Studio</span>
      <span class="brand__dot" aria-hidden="true"></span>
    </div>

    <ul class="contact-list">
      <li class="contact-list__item">
        <span class="contact-list__icon">
          <svg viewBox="0 0 24 24" aria-hidden="true"><path fill="#fff" d="M6.6 10.8a15 15 0 0 0 6.6 6.6l2.2-2.2c.3-.3.7-.4 1-.2 1.1.4 2.3.6 3.6.6.6 0 1 .4 1 1V20c0 .6-.4 1-1 1A17 17 0 0 1 3 4c0-.6.4-1 1-1h3.5c.6 0 1 .4 1 1 0 1.3.2 2.5.6 3.6.1.3 0 .7-.2 1z"/></svg>
        </span>
        916-384-7702
      </li>
      <li class="contact-list__item">
        <span class="contact-list__icon">
          <svg viewBox="0 0 24 24" aria-hidden="true"><rect x="3" y="6" width="18" height="12" rx="1" fill="#fff"/><path d="M3.5 6.5 12 13l8.5-6.5" fill="none" stroke="#0610a6" stroke-width="1.6"/></svg>
        </span>
        info@tlane-studio.example
      </li>
      <li class="contact-list__item">
        <span class="contact-list__icon">
          <svg viewBox="0 0 24 24" aria-hidden="true" fill="none" stroke="#fff" stroke-width="1.6"><circle cx="12" cy="12" r="9"/><ellipse cx="12" cy="12" rx="4" ry="9"/><path d="M3 12h18M4.5 7.5h15M4.5 16.5h15"/></svg>
        </span>
        www.tlane-studio.example
      </li>
    </ul>

    <div class="social-handle">
      <span>@t.lanestudio</span>
      <span class="social-handle__dot" aria-hidden="true"></span>
    </div>
  </section>

</main>
</body>
</html>
```